Business Card Design for company

We want new business cards. We'd like something different-- yet still highly professional. Our tagline is Providing leadership, delivering success. Stock photos are ok, as long as they are relevant and look upscale.

Target Market(s)

Architecture/Business Management Consulting/Engineering Consulting

Contact Information for Business Card

dark gray background with pops of blue might be good, but you tell me. You're the designers. Rounded corners might be nice, but again, you tell me.

Font styles to use
Serif
Sans Serif

Colors
3276b5
5c5c5c
9d9d9d
fbfbfb

Requirements
Nice to have
• Something different, but still very professional.

```html
<!DOCTYPE html>
<html lang="en">
<head>
<meta charset="utf-8">
<title>Halvern Partners – Business Card</title>
<link rel="stylesheet" href="https://fonts.googleapis.com/css2?family=Open+Sans:wght@400;600&display=swap">
<style>
  :root {
    --blue: #245a8c;
    --charcoal: #414449;
    --stripe-gray: #4d4f53;
    --paper: #f1f1f1;
    --ink: #45484d;
    --panel-text: #eceef0;
    --backdrop: #d9dadc;
  }
  * { box-sizing: border-box; margin: 0; padding: 0; }
  html, body { width: 1200px; height: 923px; overflow: hidden; }
  body {
    background: var(--backdrop);
    font-family: "Open Sans", sans-serif;
    display: flex;
    flex-direction: column;
    align-items: center;
    justify-content: center;
    gap: 60px;
  }
  .card {
    position: relative;
    width: 620px;
    height: 354px;
    background: var(--paper);
    overflow: hidden;
  }

  /* Front side */
  .card-front .edge-band {
    position: absolute; top: 0; bottom: 0; width: 16px; background: var(--blue);
  }
  .card-front .edge-line {
    position: absolute; top: 0; bottom: 0; width: 4px; background: var(--stripe-gray);
  }
  .card-front .edge-band.left { left: 0; }
  .card-front .edge-line.left { left: 26px; }
  .card-front .edge-band.right { right: 0; }
  .card-front .edge-line.right { right: 26px; }

  .brand {
    display: flex;
    align-items: center;
    gap: 14px;
    color: var(--blue);
    font-weight: 600;
    letter-spacing: 0.04em;
  }
  .brand-mark {
    width: 16px; height: 16px; background: var(--blue);
  }
  .card-front .brand {
    position: absolute; left: 50%; top: 50%;
    transform: translate(-50%, -50%);
    font-size: 40px;
    white-space: nowrap;
  }

  /* Back side */
  .card-back .logo-area {
    position: absolute; left: 0; top: 0; bottom: 0; width: 355px;
    display: flex; align-items: center; justify-content: center;
  }
  .card-back .brand { font-size: 27px; white-space: nowrap; }
  .card-back .brand-mark { width: 13px; height: 13px; }

  .contact-panel {
    position: absolute; left: 355px; right: 0; top: 0; bottom: 0;
    background: var(--charcoal);
    color: var(--panel-text);
  }
  .contact-panel .accent-strip {
    position: absolute; right: 0; top: 0; bottom: 0; width: 24px; background: var(--blue);
  }
  .person {
    position: absolute; left: 36px; top: 40px;
    padding-left: 14px;
    border-left: 6px solid var(--blue);
  }
  .person-name { font-size: 23px; font-weight: 600; line-height: 1.15; }
  .person-role { font-size: 15px; color: #c9ccd0; padding-left: 16px; }

  .contact-list {
    position: absolute; left: -12px; top: 176px;
    list-style: none;
  }
  .contact-list li {
    display: flex; align-items: flex-start; gap: 14px;
    font-size: 14px; line-height: 1.25;
    margin-bottom: 9px;
  }
  .contact-icon {
    flex: none;
    width: 24px; height: 24px;
    background: var(--blue);
    display: flex; align-items: center; justify-content: center;
  }
  .contact-icon svg { width: 15px; height: 15px; fill: none; stroke: #fff; stroke-width: 1.6; }
  .contact-text { padding-top: 3px; }
</style>
</head>
<body>

  <section class="card card-front" aria-label="Card front">
    <span class="edge-band left"></span>
    <span class="edge-line left"></span>
    <span class="edge-line right"></span>
    <span class="edge-band right"></span>
    <div class="brand"><span class="brand-mark"></span>HALVERN PARTNERS</div>
  </section>

  <section class="card card-back" aria-label="Card back">
    <div class="logo-area">
      <div class="brand"><span class="brand-mark"></span>HALVERN PARTNERS</div>
    </div>
    <div class="contact-panel">
      <span class="accent-strip"></span>
      <div class="person">
        <p class="person-name">Daniel Morrow</p>
        <p class="person-role">Owner</p>
      </div>
      <ul class="contact-list">
        <li>
          <span class="contact-icon"><svg viewBox="0 0 16 16"><path d="M4 2l2.5 3-1.5 1.5c.8 1.8 2.2 3.2 4 4L10.5 9 13.5 11.5 12 14C7 13.5 2.5 9 2 4z"/></svg></span>
          <span class="contact-text">+0000-0000-0000</span>
        </li>
        <li>
          <span class="contact-icon"><svg viewBox="0 0 16 16"><rect x="2" y="4" width="12" height="8"/><path d="M2 4l6 5 6-5"/></svg></span>
          <span class="contact-text">info@halvernpartners.com</span>
        </li>
        <li>
          <span class="contact-icon"><svg viewBox="0 0 16 16"><circle cx="8" cy="8" r="6"/><ellipse cx="8" cy="8" rx="2.6" ry="6"/><path d="M2 8h12"/></svg></span>
          <span class="contact-text">www.halvernpartners.com</span>
        </li>
        <li>
          <span class="contact-icon"><svg viewBox="0 0 16 16"><path d="M8 14s-4.5-4.6-4.5-8a4.5 4.5 0 0 1 9 0c0 3.4-4.5 8-4.5 8z"/><circle cx="8" cy="6" r="1.5"/></svg></span>
          <span class="contact-text">Suite 210,<br>48 Marlow Lane,<br>Bristol</span>
        </li>
      </ul>
    </div>
  </section>

</body>
</html>
```